Business Card Design Project

Branding and Marketing Company

Target Market(s)

Lifestyle Brands. Zorvane, Plume, Over Kestrel

Industry/Entity Type

Business

Contact Information for Business Card

I'm looking for a sleek design that is simple yet stands out. I would like to see some embossed options and even metallic features. I am looking for a black and white theme business card. Our company font is Avenir (Regular, Italic, Bold) I would like to have just the logo and the following slogan on the back of card.CREATING THE NEXT BIG THING IN HEALTH & WELLNESS

```html
<!DOCTYPE html>
<html lang="en">
<head>
<meta charset="utf-8">
<title>Velonza Business Card</title>
<link href="https://fonts.googleapis.com/css2?family=Nunito+Sans:wght@400;600;700&display=swap" rel="stylesheet">
<style>
  :root {
    --stage: #2a2a2a;
    --card-dark: #1f1d1e;
    --card-light: #ffffff;
    --card-light-shade: #e4e4e4;
    --silver: #c9c9c9;
    --silver-bright: #ededed;
    --ink: #2b2b2b;
    --soft-text: #d8d8d8;
    --rule: #ffffff;
  }
  * { margin: 0; padding: 0; box-sizing: border-box; }
  html, body { width: 1200px; height: 997px; overflow: hidden; }
  body {
    background: var(--stage);
    font-family: "Nunito Sans", sans-serif;
    position: relative;
  }
  .card {
    position: absolute;
    width: 525px;
    height: 300px;
    border-radius: 22px;
    overflow: hidden;
    background: var(--card-dark);
    box-shadow: 0 14px 30px rgba(0,0,0,0.45);
  }
  .card-back { left: 95px; top: 130px; }
  .card-front { left: 585px; top: 440px; }

  .light-panel {
    position: absolute; left: 0; top: 0; width: 100%;
    background: linear-gradient(160deg, var(--card-light) 40%, var(--card-light-shade));
  }
  .card-back .light-panel { height: 196px; }
  .card-front .light-panel { height: 138px; }

  .divider {
    position: absolute; left: 0; width: 100%; height: 3px;
    background: var(--rule);
  }
  .card-back .divider { top: 204px; }
  .card-front .divider { top: 144px; }

  .notch { position: absolute; width: 18px; height: 10px; }
  .card-back .notch { left: 254px; top: 196px; }
  .card-front .notch { left: 24px; top: 144px; }

  .brand {
    position: absolute;
    display: flex; align-items: center; gap: 12px;
    color: var(--ink);
    font-weight: 700;
  }
  .brand-dot {
    width: 30px; height: 30px; border-radius: 50%;
    background: var(--ink);
  }
  .card-back .brand { left: 0; right: 0; top: 72px; justify-content: center; font-size: 44px; }
  .card-front .brand { left: 150px; top: 44px; font-size: 42px; }

  .slogan {
    position: absolute; left: 0; right: 0; top: 226px;
    text-align: center;
    color: var(--silver-bright);
    font-weight: 700; font-size: 12px;
    letter-spacing: 1.6px;
  }
  .website-band {
    position: absolute; left: 0; right: 0; top: 258px;
    text-align: center;
    color: var(--silver);
    font-weight: 700; font-size: 13px;
    letter-spacing: 5px;
  }

  .holder { position: absolute; left: 30px; top: 160px; }
  .holder-name { color: var(--silver-bright); font-size: 20px; font-weight: 400; line-height: 1.15; }
  .holder-role { color: var(--silver); font-size: 13px; font-weight: 600; }

  .contacts { position: absolute; left: 30px; top: 210px; list-style: none; }
  .contacts li {
    display: flex; align-items: center; gap: 10px;
    color: var(--soft-text); font-size: 13px; height: 19px;
  }
  .contacts .web { color: var(--silver-bright); font-weight: 700; padding-left: 28px; }
  .icon { width: 18px; height: 18px; }

  .company { position: absolute; right: 28px; top: 170px; text-align: right; }
  .company-name { color: var(--silver-bright); font-size: 14px; font-weight: 700; }
  .company-address { color: var(--soft-text); font-size: 13px; }
</style>
</head>
<body>

  <section class="card card-back" aria-label="Card back">
    <div class="light-panel"></div>
    <div class="brand"><span class="brand-dot"></span>Velonza</div>
    <div class="divider"></div>
    <svg class="notch" viewBox="0 0 18 10"><polygon points="0,0 18,0 9,10" fill="#ffffff"/></svg>
    <p class="slogan">CREATING THE NEXT BIG THING IN HEALTH &amp; WELLNESS</p>
    <p class="website-band">www.velonza.com</p>
  </section>

  <section class="card card-front" aria-label="Card front">
    <div class="light-panel"></div>
    <div class="brand"><span class="brand-dot"></span>Velonza</div>
    <div class="divider"></div>
    <svg class="notch" viewBox="0 0 18 10"><polygon points="0,0 18,0 9,10" fill="#ffffff"/></svg>

    <div class="holder">
      <p class="holder-name">Dana Whitlock</p>
      <p class="holder-role">Licensed Electrician</p>
    </div>

    <ul class="contacts">
      <li>
        <svg class="icon" viewBox="0 0 18 18"><circle cx="9" cy="9" r="9" fill="#c9c9c9"/><path d="M6 5l2 0 1 2-1 1a5 5 0 0 0 2 2l1-1 2 1 0 2c-4 0-7-3-7-7z" fill="#1f1d1e"/></svg>
        (02) 5550 1847
      </li>
      <li>
        <svg class="icon" viewBox="0 0 18 18"><circle cx="9" cy="9" r="9" fill="#c9c9c9"/><rect x="6.5" y="4" width="5" height="10" rx="1" fill="#1f1d1e"/></svg>
        0400 555 318
      </li>
      <li>
        <svg class="icon" viewBox="0 0 18 18"><circle cx="9" cy="9" r="9" fill="#c9c9c9"/><rect x="4.5" y="6" width="9" height="6" fill="#1f1d1e"/><path d="M4.5 6l4.5 3.5 4.5-3.5" stroke="#c9c9c9" stroke-width="0.8" fill="none"/></svg>
        hello@velonza.com
      </li>
      <li class="web">www.velonza.com</li>
    </ul>

    <div class="company">
      <p class="company-name">Velonza pvt ltd.</p>
      <p class="company-address">8/22 Harbour Rd, Eastvale 2040</p>
    </div>
  </section>

</body>
</html>
```